Website Redesign for a faith-based, not-for-profit health and human services organization

New website design for the Harvest Hope Outreach House.
- Current site: www.hhohbriel.org -
We are looking for a nice clean, simple, friendly-yet-elegant website layout.
Colors are #f5eed5 (cream), #FFFFFF (white), and all logo colors.
Design a layout for home page
Design a layout for general layouts
-layout only no html needed (preferably a high res PSD file format) -
Main menu should be along top with side navigation for submenu, no side menu on home page.
Also would be open to seeing some updated colors on the logo design, currently the colors are slightly outdated. The Vine of Plenty quilt design fits the organization’s mission and the rural farming / Amish-Mennonite-Brethren community around us.

ADDITIONAL PAGES AND MENU STRUCTURE ON NEW SITE

- How to Help
... Volunteer
... Donate Time
... Donate Money
... Donate Supplies
... Current Needs

- Programs

- News & Events
... Upcoming Events
... Upcoming Fundraisers
... Newsletter

- Our Partners

- About Us
... Overview
... Mission
... Staff Directory
... Board of Directors
... Annual Reports

- Contact

Our annual special event is Gather at the Hearth and should be integrated into the home page - see attached logos and banner

Websites with elements we like (from organizations doing similar work), each for a different reason....

1. http://www.kinbridgeroutes.org
Good design, color, clarity on this site. Multi-dimensional, photos...easy interaction, etc.

2. http://endemptyplates.org
Quite simple, nothing fancy, but some good basic stuff here, and pretty easy to navigate...

3. http://www.townfolkhub.org
Intrigued by the bulletin board design and the way they have their programs broken down to show impact, needs, etc. It has a lot of good information, but is really too verbose, some of the print is too small, etc. Not perfect, but some interesting design elements.

4. http://sharedlarder.org
Site is boring and not very well designed, but it has some of the features that we would like to see at the top, donations, partners, etc.

5. http://www.bellmerefoodshelf.org
Too many listings on the sidebar - needs to be cleaner & simpler, but a lot of good information and we like the way they show volunteer photos on the Thanks to Our Helpers page...

About
Harvest Hope Outreach House ("HHOH" or “the Center”) is a faith-based non-for-profit health and human services organization that exists as an outreach of and for the Ordell-Bray Area School District.
Tagline: Mercy at Work (we work to serve the needs of the ‘least of these’ with compassion).

Mission
Our mission is to see lives transformed and the community enhanced by encouraging the oppressed, defending the cause of the weak and maintaining the rights of the poor - bringing together the resources of a caring community as a demonstration of the good news of Christ.

Company Overview
Harvest Hope Outreach House works closely with the community in which it serves. A tremendous value is placed upon the partnerships that have formed with caring people within the community and with organizations that share the goal of bringing together resources to help those who need it most. Individuals, volunteers, churches, corporations, foundations, and government sources all pull together to help make our mission possible.

Since 1996 the Harvest Hope Outreach House has collaboratively worked to see our community enhanced, adapting programs and services to meet the changing needs of the community.

Target Market(s)

people needing assistance in local community

Industry/Entity Type

Government

Requirements
Must have
• Good social button integration
Should not have
• No Find Us page like old website it is not needed

```html
<!DOCTYPE html>
<html lang="en">
<head>
<meta charset="utf-8">
<title>Harvest Hope Outreach House</title>
<link href="https://fonts.googleapis.com/css2?family=Open+Sans:wght@400;600;700&display=swap" rel="stylesheet">
<style>
:root{
  --cream:#f5eed5;
  --cream-light:#fbf7e8;
  --maroon:#7a1a2c;
  --maroon-dark:#6a1224;
  --maroon-bright:#a8223c;
  --charcoal:#333333;
  --charcoal-line:#4a4a4a;
  --text:#3a3a3a;
  --muted:#888;
  --lime:#c9c83a;
  --lime-dark:#a6a51e;
  --rule:#d9d0b4;
  --footer-text:#c9c9c9;
}
*{box-sizing:border-box;margin:0;padding:0}
html,body{width:1131px;height:1200px;overflow:hidden;background:var(--cream)}
body{font-family:"Open Sans",Arial,sans-serif;color:var(--text)}
.stage{position:relative;width:1020px;height:1082px;transform:scale(1.1088);transform-origin:0 0;background:var(--cream)}
.abs{position:absolute}
a{color:inherit;text-decoration:none}

/* brand */
.brand{left:45px;top:22px;display:flex;align-items:center;gap:12px}
.brand-mark{width:66px;height:66px;background:var(--maroon)}
.brand-name{font-size:20px;line-height:21px;font-weight:400;color:var(--maroon);width:130px}

/* social */
.follow{left:856px;top:39px;font-size:9px;font-weight:700;color:#444;letter-spacing:.3px}
.social{top:30px;width:28px;height:28px;border-radius:4px;background:#e7e3d6;border:1px solid #cfc9b6}

/* nav */
.main-nav{left:31px;top:138px;width:960px;height:30px;border-radius:15px;
  background:linear-gradient(#b02a45,var(--maroon) 55%,var(--maroon-dark));display:flex}
.main-nav a{color:#fff;font-size:13px;font-weight:700;display:flex;align-items:center;justify-content:center;height:30px;border-right:1px solid #5a0f1e;box-shadow:1px 0 0 #b6344e}
.main-nav a:last-child{border:0;box-shadow:none}

/* newsletter */
.newsletter{left:30px;top:196px;width:198px;height:313px;background:var(--charcoal)}
.newsletter-head{height:108px;border-bottom:1px solid var(--charcoal-line);text-align:center;padding-top:30px;color:var(--lime)}
.newsletter-head .small{font-size:18px;line-height:20px}
.newsletter-head .big{font-size:29px;line-height:32px}
.newsletter label{display:block;color:#9a9a9a;font-size:12px;margin:0 0 5px 18px}
.newsletter .field{display:block;width:160px;height:20px;background:#fff;margin:0 0 12px 18px}
.signup{margin:4px 0 0 18px;width:90px;height:30px;background:linear-gradient(#d6d54a,var(--lime-dark));font-size:12px;font-weight:700;color:#222;display:flex;align-items:center;justify-content:center}

/* photos */
.photo{width:120px;height:120px}

.headline{left:270px;top:336px;font-size:27px;font-weight:400;color:var(--maroon)}
.lead{left:272px;top:389px;width:665px;font-size:13px;line-height:18.5px}
.btn{height:24px;border-radius:12px;background:linear-gradient(var(--maroon-bright),var(--maroon-dark));color:#fff;font-size:13px;font-weight:700;display:flex;align-items:center;justify-content:center}
.rule{height:1px;background:var(--rule)}

/* side panels */
.panel-head{height:40px;background:linear-gradient(#b0304a,var(--maroon-dark));color:#fff;font-size:13px;font-weight:700;padding:12px 0 0 22px}
.panel-box{border:1px solid #c27a86;border-top:0;background:radial-gradient(ellipse at center,var(--cream-light),var(--cream) 80%)}

.testimonial{left:53px;display:flex;gap:6px;width:160px;overflow:hidden}
.thumb-sm{width:42px;height:42px;flex:none}
.item-title{font-size:13px;font-weight:700;color:var(--maroon);line-height:16px;white-space:nowrap}
.item-text{font-size:12px;line-height:13px;white-space:nowrap}
.item-text b{color:var(--maroon);font-size:11px}

.feature-title{font-size:15px;font-weight:700;color:var(--maroon)}
.feature-text{width:205px;font-size:13px;line-height:19px}

.help-item{left:738px;display:flex;gap:10px}
.thumb-md{width:70px;height:60px;flex:none}
.help-date{font-size:10px;color:var(--muted);line-height:14px}
.help-text{font-size:12px;line-height:15px;width:150px}
.help-text b{color:var(--maroon)}

/* footer */
.footer{left:0;top:942px;width:1020px;height:140px;background:var(--charcoal)}
.footer-nav{left:31px;top:25px;font-size:12px;color:var(--footer-text)}
.footer-nav span{margin:0 9px;color:#888}
.footer-line{left:0;top:98px;width:1020px;height:1px;background:#555}
.copyright{left:32px;top:111px;font-size:12px;color:#aaa}
.legal{right:32px;top:111px;font-size:12px;color:#aaa}
</style>
</head>
<body>
<div class="stage">

  <a class="abs brand" href="#"><span class="brand-mark"></span><span class="brand-name">Harvest Hope Outreach House</span></a>

  <div class="abs follow">FOLLOW US</div>
  <a class="abs social" style="left:925px" href="#" aria-label="Social network one"></a>
  <a class="abs social" style="left:958px" href="#" aria-label="Social network two"></a>

  <nav class="abs main-nav">
    <a href="#" style="width:120px">Home</a>
    <a href="#" style="width:144px">How to Help</a>
    <a href="#" style="width:129px">Programs</a>
    <a href="#" style="width:162px">News &amp; Events</a>
    <a href="#" style="width:151px">Our Partners</a>
    <a href="#" style="width:125px">About Us</a>
    <a href="#" style="width:129px">Contact</a>
  </nav>

  <section class="abs newsletter">
    <div class="newsletter-head"><div class="small">NEWSLETTER</div><div class="big">SIGNUP</div></div>
    <div style="padding-top:28px">
      <label>Name</label><span class="field"></span>
      <label>Email</label><span class="field"></span>
      <div class="signup">SIGN UP</div>
    </div>
  </section>

  <div class="abs photo" style="left:270px;top:196px;background:linear-gradient(#9aa58a,#7d6a52)" role="img" aria-label="Volunteers holding grocery bags"></div>
  <div class="abs photo" style="left:420px;top:196px;background:linear-gradient(#6b6358,#b8a58a)" role="img" aria-label="Volunteers preparing food in a kitchen"></div>
  <div class="abs photo" style="left:570px;top:196px;background:linear-gradient(#c9c0b0,#a33a3e)" role="img" aria-label="Two volunteers in red shirts"></div>
  <div class="abs photo" style="left:720px;top:196px;background:linear-gradient(#c7ccd2,#5b6470)" role="img" aria-label="Volunteer carrying a box from a trailer"></div>
  <div class="abs photo" style="left:870px;top:196px;background:linear-gradient(#8a6a3e,#3a4a6a)" role="img" aria-label="Crowded community dinner in a hall"></div>

  <h1 class="abs headline">Convenire scripserit est cu, his reque offendit</h1>
  <p class="abs lead">Nominati definiebas percipitur at vis. Ferri atqui vim ex, ex adhuc oratio mea. Consul alterum urbanitas an vix. Ex mundi inimicus pri, quo ne quis magna. Usu erant congue te, eum labores blandit eu. Qui nullam admodum petentium cu, quas moderatius dissentiunt vel at, fugit graeci voluptaria per no.</p>
  <a class="abs btn" href="#" style="left:272px;top:467px;width:130px">Read more</a>
  <div class="abs rule" style="left:270px;top:519px;width:720px"></div>

  <div class="abs panel-head" style="left:30px;top:540px;width:198px">TESTIMONIALS</div>
  <div class="abs panel-box" style="left:36px;top:580px;width:185px;height:298px"></div>
  <div class="abs testimonial" style="top:602px"><div class="thumb-sm" style="background:linear-gradient(#a9a39a,#8a3a3a)" role="img" aria-label="Testimonial photo"></div><div><div class="item-title">Title Goes Here</div><div class="item-text">Nominati definiebas<br>rebus. <b>Read more</b></div></div></div>
  <div class="abs testimonial" style="top:669px"><div class="thumb-sm" style="background:linear-gradient(#a9a39a,#8a3a3a)" role="img" aria-label="Testimonial photo"></div><div><div class="item-title">Title Goes Here</div><div class="item-text">Nominati definiebas<br>rebus. <b>Read more</b></div></div></div>
  <div class="abs testimonial" style="top:735px"><div class="thumb-sm" style="background:linear-gradient(#a9a39a,#8a3a3a)" role="img" aria-label="Testimonial photo"></div><div><div class="item-title">Title Goes Here</div><div class="item-text">Nominati definiebas<br>rebus. <b>Read more</b></div></div></div>
  <div class="abs testimonial" style="top:805px"><div class="thumb-sm" style="background:linear-gradient(#a9a39a,#8a3a3a)" role="img" aria-label="Testimonial photo"></div><div><div class="item-title">Title Goes Here</div><div class="item-text">Nominati definiebas<br>rebus. <b>Read more</b></div></div></div>

  <div class="abs" style="left:247px;top:562px;width:220px;height:115px;border-radius:8px;background:linear-gradient(#e58a4a,#f1d79a)" role="img" aria-label="Gather at the Hearth event illustration"></div>
  <h2 class="abs feature-title" style="left:485px;top:557px">Another Title Goes Here</h2>
  <p class="abs feature-text" style="left:486px;top:584px">Nominati definiebas percipitur at vis. Ferri atqui vim ex, ex adhuc oratio mea. Consul alterum</p>
  <a class="abs btn" href="#" style="left:485px;top:649px;width:130px">Read more</a>
  <div class="abs rule" style="left:270px;top:708px;width:420px"></div>

  <div class="abs" style="left:265px;top:740px;width:200px;height:115px;background:linear-gradient(#8a8478,#a84a4a 60%,#d8c8a8)" role="img" aria-label="Group of volunteers at a supply drive"></div>
  <h2 class="abs feature-title" style="left:485px;top:738px">Another Title Goes Here</h2>
  <p class="abs feature-text" style="left:486px;top:765px">Nominati definiebas percipitur at vis. Ferri atqui vim ex, ex adhuc oratio mea. Consul alterum</p>
  <a class="abs btn" href="#" style="left:485px;top:830px;width:130px">Read more</a>
  <div class="abs rule" style="left:270px;top:878px;width:420px"></div>

  <div class="abs panel-head" style="left:715px;top:540px;width:275px">HOW TO HELP</div>
  <div class="abs panel-box" style="left:720px;top:580px;width:265px;height:299px"></div>
  <div class="abs help-item" style="top:606px"><div class="thumb-md" style="background:linear-gradient(#9a9488,#8a3a3a)" role="img" aria-label="Volunteers at a food drive"></div><div><div class="item-title" style="font-size:14px">Title Goes Here</div><div class="help-date">25 Feb 2013</div><div class="help-text">Nominati definiebas rebus percipitur vis. &nbsp;<b>Read more</b></div></div></div>
  <div class="abs help-item" style="top:693px"><div class="thumb-md" style="background:linear-gradient(#7a7a6e,#c94a4a)" role="img" aria-label="Child holding a sign"></div><div><div class="item-title" style="font-size:14px">Title Goes Here</div><div class="help-date">25 Feb 2013</div><div class="help-text">Nominati definiebas rebus percipitur vis. &nbsp;<b>Read more</b></div></div></div>
  <div class="abs help-item" style="top:780px"><div class="thumb-md" style="background:linear-gradient(#b8ab96,#e8e2d8)" role="img" aria-label="Two volunteers smiling"></div><div><div class="item-title" style="font-size:14px">Title Goes Here</div><div class="help-date">25 Feb 2013</div><div class="help-text">Nominati definiebas rebus percipitur vis. &nbsp;<b>Read more</b></div></div></div>

  <footer class="abs footer">
    <nav class="abs footer-nav">Home<span>|</span>How to Help<span>|</span>Programs<span>|</span>News &amp; Events<span>|</span>Our Partners<span>|</span>About Us<span>|</span>Contact</nav>
    <div class="abs footer-line"></div>
    <div class="abs copyright">Copyright © Harvest Hope Outreach House &nbsp; - &nbsp; All Rights Reserved</div>
    <div class="abs legal">Privacy Policy &nbsp;|&nbsp; Ethics Policy</div>
  </footer>

</div>
</body>
</html>
```